Oil and Gas Exploration and Production company needs a business card design

We need a business card design using our logo and colors in the logo. We want a mainstream design.

```html
<!DOCTYPE html>
<html lang="en">
<head>
<meta charset="utf-8">
<title>Sorata Oil &amp; Gas – Business Card</title>
<link rel="stylesheet" href="https://fonts.googleapis.com/css2?family=Roboto+Slab:wght@400;700;800&family=Roboto:wght@400&display=swap">
<style>
  :root {
    --backdrop: #e4e0da;
    --card: #f4f4f2;
    --ink: #231f20;
    --ink-soft: #3b3838;
    --gold: #c4993a;
    --muted: #555;
  }
  * { box-sizing: border-box; margin: 0; padding: 0; }
  html, body { width: 1200px; height: 960px; overflow: hidden; }
  body {
    position: relative;
    background: var(--backdrop);
    font-family: "Roboto Slab", serif;
    color: var(--ink);
  }
  .card {
    position: absolute;
    width: 600px;
    height: 343px;
    background: var(--card);
    box-shadow: 0 2px 5px rgba(0,0,0,0.25);
  }
  .card--front { left: 314px; top: 113px; }
  .card--back { left: 311px; top: 472px; }

  .holder { position: absolute; left: 41px; top: 116px; }
  .holder__name {
    font-weight: 800;
    font-size: 20px;
    letter-spacing: 0.5px;
    line-height: 1;
  }
  .holder__role {
    margin-top: 5px;
    font-size: 13px;
    color: var(--gold);
    letter-spacing: 0.3px;
  }
  .address {
    margin-top: 19px;
    font-size: 13px;
    line-height: 19px;
    color: var(--ink-soft);
  }
  .contacts {
    list-style: none;
    margin-top: 12px;
    font-size: 13px;
    line-height: 19.2px;
    color: var(--ink-soft);
  }
  .contacts li { display: flex; align-items: center; gap: 8px; }
  .contacts svg { width: 13px; height: 13px; fill: var(--ink); flex: none; }

  .brand-mark {
    position: absolute;
    right: 20px;
    top: 20px;
    width: 225px;
    height: 305px;
    display: flex;
    flex-direction: column;
    align-items: center;
    justify-content: center;
    gap: 18px;
  }
  .brand-mark__dot {
    width: 150px; height: 150px; border-radius: 50%;
    background: var(--ink);
  }
  .brand-mark__name {
    font-weight: 800;
    font-size: 40px;
    color: var(--ink);
    line-height: 1;
  }

  .wordmark {
    position: absolute;
    left: 0; right: 0; top: 120px;
    display: flex;
    align-items: center;
    justify-content: center;
    gap: 14px;
  }
  .wordmark__dot {
    width: 40px; height: 40px; border-radius: 50%;
    background: var(--ink);
  }
  .wordmark__name {
    font-weight: 800;
    font-size: 52px;
    line-height: 1;
    color: var(--ink);
  }
  .back__url {
    position: absolute;
    left: 0; right: 0; top: 288px;
    text-align: center;
    font-family: "Roboto", sans-serif;
    font-size: 14px;
    letter-spacing: 4.3px;
    color: var(--muted);
  }
</style>
</head>
<body>
  <section class="card card--front">
    <div class="holder">
      <h1 class="holder__name">DANIEL HART</h1>
      <p class="holder__role">CEO/FOUNDER</p>
      <p class="address">2140 Birchwood Road<br>Juneau, Alaska 34812</p>
      <ul class="contacts">
        <li><svg viewBox="0 0 16 16"><path d="M3.6 1 6 3.8 4.6 5.6c.9 2 2.6 3.8 4.8 4.8L11.2 9 14 11.4 12.6 14C7 14 2 9 2 3.4z"/></svg>614 208 5173</li>
        <li><svg viewBox="0 0 16 16"><path d="M4 0h8a1 1 0 0 1 1 1v14a1 1 0 0 1-1 1H4a1 1 0 0 1-1-1V1a1 1 0 0 1 1-1zm1 2v10h6V2zm3 11a1 1 0 1 0 0 2 1 1 0 0 0 0-2z"/></svg>827 319 4056</li>
        <li><svg viewBox="0 0 16 16"><path d="M4 1h8v4H4zM1 6h14v6h-2v3H3v-3H1zm4 5v3h6v-3z"/></svg>493 762 1185</li>
        <li><svg viewBox="0 0 16 16"><path d="M1 3h14v1L8 9 1 4zm0 2.5 7 5 7-5V13H1z"/></svg>info@sorataoil&amp;gas.com</li>
        <li><svg viewBox="0 0 16 16"><path d="M8 1a7 7 0 1 0 0 14A7 7 0 0 0 8 1zm-1 2.2C6 4.5 5.2 5 5.5 6.5s2 1.3 2.3 2.4-.8 2.1-.4 3.6c-2.5-.5-4-2.6-4-4.6 0-2 1.4-4 3.6-4.7zm3 .3c1.6.8 2.7 2.3 2.8 4-.9-.4-1.7-.2-2.2.6-.4-1.2-1.4-1-1.4-2.2 0-1 .9-1.3.8-2.4z"/></svg>www.sorataoil&amp;gas.com</li>
      </ul>
    </div>
    <div class="brand-mark">
      <span class="brand-mark__dot"></span>
      <span class="brand-mark__name">Sorata</span>
    </div>
  </section>

  <section class="card card--back">
    <div class="wordmark">
      <span class="wordmark__dot"></span>
      <span class="wordmark__name">Sorata Oil &amp; Gas</span>
    </div>
    <p class="back__url">www.sorataoil&amp;gas.com</p>
  </section>
</body>
</html>
```